Website for vegan focused blog

A website is needed so that I can launch my new blog in Dubai. It will be mainly vegan focused but also lifestyle based. Wordpress based- i started to build a site on Wordpress but design is not my forte ;)
Main content on the site will be; my recipes, reviews of products/restaurants, lifestyle posts and travel.
For this I ask for a homepage design, a recipe design page that includes a recipe card and a generic page for posts that can show pictures and videos. Also a contact me page.
Main headers should be: Home, Recipes and happy for suggestions.
Must look clean and neat but appealing, happy for minimalist look. I like pink and grey colours. Must be Wordpress compatible.
Have attached a couple of example posts for reference
Must have social links etc.
name of blog is: Maren by the dunes
Other blogs I like are: https://quietladleoven.com/ https://wellfernkitchen.com/ https://wellfernkitchen.com/ https://www.ohladycakes.com/https://beetsatsupper.com/ https://dorintalve.com/

Target Market(s)

Residents in the UAE. General individuals interested in vegan meals, plant based nutrition, travel and reviews.

Number of Pages Required

4 page

Colors
eea4c8
eda3c7
f9d9e8
dbdbdb
aaaaaa
d5d5d5

Requirements
Must have
• Recipe page- must include recipe card plug in option
• Social media integration
• Email sign ups

```html
<!DOCTYPE html>
<html lang="en">
<head>
<meta charset="utf-8">
<title>Maren by the dunes</title>
<link href="https://fonts.googleapis.com/css2?family=Montserrat:wght@400;500;600;700&family=Open+Sans:wght@400;600&display=swap" rel="stylesheet">
<style>
:root{
  --pink:#eea4c8;
  --pink-soft:#f9d9e8;
  --ink:#1f1f1f;
  --text:#6d6d6d;
  --line:#dbdbdb;
  --grey:#aaaaaa;
  --footer:#a7a7a7;
  --white:#ffffff;
}
*{margin:0;padding:0;box-sizing:border-box}
html,body{width:1200px;height:4455px;overflow:hidden;background:var(--white)}
body{position:relative;font-family:"Open Sans",Arial,sans-serif;color:var(--text)}
.abs{position:absolute}

/* header */
.site-header{position:absolute;left:0;top:0;width:1200px;height:90px}
.logo{left:110px;top:32px;font-family:"Montserrat",sans-serif;font-weight:700;font-size:22px;color:var(--ink);text-transform:uppercase;letter-spacing:.5px}
.nav{left:690px;top:36px;display:flex;font-family:"Montserrat",sans-serif;font-weight:600;font-size:14px;text-transform:uppercase}
.nav a{color:var(--ink);text-decoration:none;margin-right:42px}
.nav a.active{color:var(--pink)}
.search{left:1070px;top:35px}

/* hero */
.hero{left:0;top:90px;width:1200px;height:568px;background:radial-gradient(ellipse at 45% 30%,#b89478 0%,#6e5a4d 35%,#3b3532 70%,#8a7068 100%)}
.hero-title{left:0;top:235px;width:1200px;text-align:center;font-family:"Montserrat",sans-serif;font-weight:700;font-size:62px;color:var(--white);text-transform:uppercase;letter-spacing:1px}
.hero-sub{left:0;top:328px;width:1200px;text-align:center;font-size:21px;color:var(--white)}
.hero-btn{left:493px;top:398px;width:214px;height:56px;border:2px solid var(--white);border-radius:30px;color:var(--white);font-family:"Montserrat",sans-serif;font-weight:600;font-size:15px;text-transform:uppercase;display:flex;align-items:center;justify-content:center}
.dots{left:560px;top:556px;display:flex;gap:6px}
.dots span{width:13px;height:13px;border-radius:50%;border:2px solid var(--white)}
.dots span.on{background:var(--white)}

/* meta icons */
.meta{display:flex;align-items:center;gap:8px;color:var(--text);white-space:nowrap}
.meta .sep{color:var(--grey)}
.ico-date{width:12px;height:12px;border:1.5px solid var(--pink);border-top-width:4px;flex:none}
.ico-user{width:11px;height:12px;flex:none;background:radial-gradient(circle at 50% 28%,var(--pink) 0 3px,transparent 3.5px),radial-gradient(ellipse at 50% 110%,var(--pink) 0 6px,transparent 6.5px)}

/* posts */
.post{left:110px;width:582px}
.post-title{font-family:"Montserrat",sans-serif;font-weight:500;font-size:25px;line-height:39px;color:var(--ink);text-transform:uppercase;white-space:nowrap}
.post .meta{margin-top:16px;font-size:14px}
.post-img{margin-top:26px;width:582px;height:385px}
.excerpt{margin-top:30px;font-size:13.5px;line-height:28px}
.read-more{margin-top:32px;width:140px;height:50px;border:2px solid var(--pink);border-radius:26px;color:var(--pink);font-family:"Montserrat",sans-serif;font-weight:600;font-size:14px;text-transform:uppercase;display:flex;align-items:center;justify-content:center}

/* sidebar */
.about{left:747px;top:750px;width:338px;height:338px;background:var(--pink);padding:28px 28px;color:var(--white)}
.about h3{font-family:"Montserrat",sans-serif;font-weight:700;font-size:22px;line-height:30px;text-transform:uppercase}
.about p{margin-top:16px;font-size:12.5px;line-height:24px}
.about .more{margin-top:14px;font-family:"Montserrat",sans-serif;font-weight:600;font-size:14px;text-transform:uppercase}
.side-title{left:747px;font-family:"Montserrat",sans-serif;font-weight:700;font-size:22px;color:var(--ink);text-transform:uppercase}
.side-item{left:747px;width:338px;display:flex;gap:21px}
.thumb{width:112px;height:80px;flex:none}
.side-item h4{font-family:"Montserrat",sans-serif;font-weight:500;font-size:16px;line-height:23px;color:var(--ink);white-space:nowrap}
.side-item .meta{margin-top:8px;font-size:12.5px}
.view-more{left:747px;font-family:"Montserrat",sans-serif;font-weight:600;font-size:15px;color:var(--pink);text-transform:uppercase}
.rule{left:747px;width:338px;height:2px;background:var(--line)}

.follow-card{left:747px;top:2370px;width:338px;height:267px;border:2px solid var(--line)}
.follow-cover{left:6px;top:6px;width:322px;height:146px;background:linear-gradient(120deg,#c9a9a9,#8c6f70 60%,#b79591)}
.follow-badge{left:18px;top:18px;width:70px;height:70px;background:var(--white);padding:8px;font-family:"Montserrat",sans-serif;font-weight:700;font-size:11px;line-height:14px;color:var(--ink);text-transform:uppercase}
.follow-name{left:100px;top:20px;color:var(--white);font-family:"Montserrat",sans-serif;font-weight:600;font-size:14px;text-transform:uppercase}
.follow-count{left:100px;top:40px;color:var(--white);font-size:11px}
.follow-btn{left:232px;top:112px;width:84px;height:26px;background:var(--white);border-radius:13px;font-family:"Montserrat",sans-serif;font-size:12px;font-weight:600;color:var(--pink);display:flex;align-items:center;justify-content:center;text-transform:uppercase}
.follow-note{left:18px;top:170px;font-size:11.5px;color:var(--text)}
.followers{left:18px;top:198px;display:flex;gap:4px}
.followers span{width:47px;height:47px}

/* footer */
.site-footer{left:0;top:4030px;width:1200px;height:425px;background:var(--footer);color:var(--white)}
.f-col{top:94px}
.f-col h5{font-family:"Montserrat",sans-serif;font-weight:600;font-size:18px;text-transform:uppercase;letter-spacing:.5px}
.f-col ul{list-style:none;margin-top:22px;font-size:12.5px;line-height:24px}
.f-contact{font-size:12.5px;line-height:20px;margin-top:26px}
.f-contact div{display:flex;gap:14px;margin-bottom:22px}
.email-field{margin-top:22px;width:275px;height:36px;background:var(--white);color:var(--grey);font-size:12.5px;padding:0 10px;display:flex;align-items:center}
.subscribe{margin-top:20px;width:106px;height:36px;border-radius:20px;background:var(--pink);font-family:"Montserrat",sans-serif;font-weight:600;font-size:12px;text-transform:uppercase;display:flex;align-items:center;justify-content:center}
.f-rule{left:110px;top:324px;width:975px;height:1px;background:#c4c4c4}
.copy{left:110px;top:356px;font-size:12.5px}
.socials{left:925px;top:343px;display:flex;gap:12px}
.socials span{width:34px;height:34px;border:2px solid var(--white);border-radius:50%}
</style>
</head>
<body>

<header class="site-header">
  <div class="abs logo">Maren by the dunes</div>
  <nav class="abs nav">
    <a class="active">Home</a><a>Recipe</a><a>Blog</a><a>Contact</a>
  </nav>
  <svg class="abs search" width="18" height="18" viewBox="0 0 18 18" aria-label="Search"><circle cx="7.5" cy="7.5" r="5.5" fill="none" stroke="#1f1f1f" stroke-width="2.4"/><line x1="11.5" y1="11.5" x2="16.5" y2="16.5" stroke="#1f1f1f" stroke-width="2.6" stroke-linecap="round"/></svg>
</header>

<section class="abs hero" role="img" aria-label="Bowl of roasted baby potatoes with rosemary and garlic on a wooden table"></section>
<h1 class="abs hero-title">Maren by the dunes</h1>
<p class="abs hero-sub">At vero eos et accusamus et iusto odio dignissimos ducimus qui</p>
<div class="abs hero-btn">Get more info</div>
<div class="abs dots"><span class="on"></span><span></span><span></span><span></span></div>

<article class="abs post" style="top:735px">
  <h2 class="post-title">Nam libero tempore cum soluta lib<br>nobis est eligendi</h2>
  <div class="meta"><span class="ico-date"></span>01/09/08<span class="sep">|</span><span class="ico-user"></span>John</div>
  <div class="post-img" role="img" aria-label="Hands serving green salad from a bowl with wooden tongs" style="background:linear-gradient(135deg,#e8e4df,#9a8a7a 45%,#3f5f2c 70%,#b4302c)"></div>
  <p class="excerpt">At vero eos et accusamus et iusto odio dignissimos ducimus qui blanditiis praesentium voluptatum deleniti atque corrupti quos dolores et quas molestias excepturi sint occaecati cupiditate non provident, similique sunt in culpa qui officia deserunt mollitia animi, id est laborum et dolorum fuga. Et harum quidem rerum facilis.</p>
  <div class="read-more">Read more</div>
</article>

<article class="abs post" style="top:1560px">
  <h2 class="post-title">Nam libero tempore cum soluta lib<br>nobis est eligendi</h2>
  <div class="meta"><span class="ico-date"></span>01/09/08<span class="sep">|</span><span class="ico-user"></span>John</div>
  <div class="post-img" role="img" aria-label="Stack of vegetable patties with lettuce on a blue surface" style="background:linear-gradient(150deg,#5d6f8a,#7b4a2c 40%,#5a3319 60%,#9bc66a 85%)"></div>
  <p class="excerpt">At vero eos et accusamus et iusto odio dignissimos ducimus qui blanditiis praesentium voluptatum deleniti atque corrupti quos dolores et quas molestias excepturi sint occaecati cupiditate non provident, similique sunt in culpa qui officia deserunt mollitia animi, id est laborum et dolorum fuga. Et harum quidem rerum facilis.</p>
  <div class="read-more">Read more</div>
</article>

<article class="abs post" style="top:2352px">
  <h2 class="post-title">Nam libero tempore cum soluta lib<br>nobis est eligendi</h2>
  <div class="meta"><span class="ico-date"></span>01/09/08<span class="sep">|</span><span class="ico-user"></span>John</div>
  <div class="post-img" role="img" aria-label="Avocado, tomatoes, peppers and greens on a wooden table seen from above" style="background:linear-gradient(120deg,#6b4a31,#a8713f 40%,#5b7a2e 65%,#7a4d2d)"></div>
  <p class="excerpt">At vero eos et accusamus et iusto odio dignissimos ducimus qui blanditiis praesentium voluptatum deleniti atque corrupti quos dolores et quas molestias excepturi sint occaecati cupiditate non provident, similique sunt in culpa qui officia deserunt mollitia animi, id est laborum et dolorum fuga. Et harum quidem rerum facilis.</p>
  <div class="read-more">Read more</div>
</article>

<article class="abs post" style="top:3166px">
  <h2 class="post-title">Nam libero tempore cum soluta lib<br>nobis est eligendi</h2>
  <div class="meta"><span class="ico-date"></span>01/09/08<span class="sep">|</span><span class="ico-user"></span>John</div>
  <div class="post-img" role="img" aria-label="Potato salad with herbs in a dark bowl" style="background:radial-gradient(ellipse at 50% 55%,#d9b27c,#8c6a45 45%,#2e2a27 80%)"></div>
  <p class="excerpt">At vero eos et accusamus et iusto odio dignissimos ducimus qui blanditiis praesentium voluptatum deleniti atque corrupti quos dolores et quas molestias excepturi sint occaecati cupiditate non provident, similique sunt in culpa qui officia deserunt mollitia animi, id est laborum et dolorum fuga. Et harum quidem rerum facilis.</p>
  <div class="read-more">Read more</div>
</article>

<aside>
  <div class="abs about">
    <h3>About<br>Maren by the dunes</h3>
    <p>On Maren by the dunes, I share some delicious recipes either my own or from other fabulous sites that I have come across, my meal plans, reviews of products and restaurants that I visit and more.<br>And yes, I live on a plant based diet. Shock...horror...shakes on...leaves eat...!</p>
    <div class="more">Read more</div>
  </div>

  <h3 class="abs side-title" style="top:1150px">Latest news</h3>
  <div class="abs side-item" style="top:1206px"><div class="thumb" role="img" aria-label="Green salad plate" style="background:linear-gradient(135deg,#3f5f2c,#8a9a4a,#b4302c)"></div><div><h4>Nam libero tempore cum<br>soluta nob olupt</h4><div class="meta"><span class="ico-date"></span>01/09/08<span class="sep">|</span><span class="ico-user"></span>John</div></div></div>
  <div class="abs side-item" style="top:1310px"><div class="thumb" role="img" aria-label="Colourful salad bowl" style="background:linear-gradient(135deg,#c84b4b,#d9d0c0,#6a8a3a)"></div><div><h4>Nam libero tempore cum<br>soluta nob olupt</h4><div class="meta"><span class="ico-date"></span>01/09/08<span class="sep">|</span><span class="ico-user"></span>John</div></div></div>
  <div class="abs side-item" style="top:1414px"><div class="thumb" role="img" aria-label="Green beans on a plate" style="background:linear-gradient(135deg,#2f4a1e,#6b9a3a,#e0c070)"></div><div><h4>Nam libero tempore cum<br>soluta nob olupt</h4><div class="meta"><span class="ico-date"></span>01/09/08<span class="sep">|</span><span class="ico-user"></span>John</div></div></div>
  <div class="abs side-item" style="top:1518px"><div class="thumb" role="img" aria-label="Potato salad" style="background:linear-gradient(135deg,#d7c08a,#9aa36a,#e8e2d0)"></div><div><h4>Nam libero tempore cum<br>soluta nob olupt</h4><div class="meta"><span class="ico-date"></span>01/09/08<span class="sep">|</span><span class="ico-user"></span>John</div></div></div>
  <div class="abs view-more" style="top:1622px">View more</div>
  <div class="abs rule" style="top:1674px"></div>

  <h3 class="abs side-title" style="top:1734px">Most popular</h3>
  <div class="abs side-item" style="top:1790px"><div class="thumb" role="img" aria-label="Serving salad" style="background:linear-gradient(135deg,#e8e4df,#6f7a4a,#b4302c)"></div><div><h4>Nam libero tempore cum<br>soluta nob olupt</h4><div class="meta"><span class="ico-date"></span>01/09/08<span class="sep">|</span><span class="ico-user"></span>John</div></div></div>
  <div class="abs side-item" style="top:1894px"><div class="thumb" role="img" aria-label="Fresh salad" style="background:linear-gradient(135deg,#c84b4b,#7aa04a,#e9e4da)"></div><div><h4>Nam libero tempore cum<br>soluta nob olupt</h4><div class="meta"><span class="ico-date"></span>01/09/08<span class="sep">|</span><span class="ico-user"></span>John</div></div></div>
  <div class="abs side-item" style="top:1998px"><div class="thumb" role="img" aria-label="Vegetable patties" style="background:linear-gradient(135deg,#5d6f8a,#7b4a2c,#9bc66a)"></div><div><h4>Nam libero tempore cum<br>soluta nob olupt</h4><div class="meta"><span class="ico-date"></span>01/09/08<span class="sep">|</span><span class="ico-user"></span>John</div></div></div>
  <div class="abs side-item" style="top:2102px"><div class="thumb" role="img" aria-label="Green salad bowl" style="background:linear-gradient(135deg,#2f4a1e,#6b9a3a,#c84b4b)"></div><div><h4>Nam libero tempore cum<br>soluta nob olupt</h4><div class="meta"><span class="ico-date"></span>01/09/08<span class="sep">|</span><span class="ico-user"></span>John</div></div></div>
  <div class="abs view-more" style="top:2203px">View more</div>

  <h3 class="abs side-title" style="top:2320px">Follow us</h3>
  <div class="abs follow-card">
    <div class="abs follow-cover" role="img" aria-label="Cover photo of roasted vegetables"></div>
    <div class="abs follow-badge">Maren by the dunes</div>
    <div class="abs follow-name">Maren by the dunes</div>
    <div class="abs follow-count">210 followers</div>
    <div class="abs follow-btn">Follow</div>
    <div class="abs follow-note">Join our community of plant based cooks</div>
    <div class="abs followers" role="img" aria-label="Follower photos">
      <span style="background:#6b5b55"></span><span style="background:#8d7468"></span><span style="background:#4d4a55"></span><span style="background:#a88070"></span><span style="background:#5f6a70"></span><span style="background:#7a6555"></span>
    </div>
  </div>
</aside>

<footer class="abs site-footer">
  <div class="abs f-col" style="left:110px">
    <h5>Information</h5>
    <ul><li>Home</li><li>About</li><li>Recipe</li><li>Blog</li><li>Contact</li></ul>
  </div>
  <div class="abs f-col" style="left:320px">
    <h5>Quick links</h5>
    <ul><li>Help</li><li>FAQ</li><li>Support</li><li>Sitemap</li><li>Terms and Conditions</li><li>Privacy Statement</li></ul>
  </div>
  <div class="abs f-col" style="left:528px">
    <h5>Contact us</h5>
    <div class="f-contact">
      <div><svg width="14" height="14" viewBox="0 0 14 14"><path d="M3 1l2.5 3-1.5 1.5c.8 1.8 2.2 3.2 4 4L9.5 8l3 2.5-1.5 2.5C6 12.5 1.5 8 1 2.5z" fill="#fff"/></svg>+971 4 555 0188</div>
      <div><svg width="14" height="12" viewBox="0 0 14 12"><rect x="0.5" y="0.5" width="13" height="11" fill="#fff"/><path d="M1 1l6 5 6-5" fill="none" stroke="#a7a7a7" stroke-width="1.2"/></svg>hello@marenbythedunes.com</div>
      <div><svg width="12" height="16" viewBox="0 0 12 16"><path d="M6 0C2.7 0 0 2.6 0 5.8 0 10 6 16 6 16s6-6 6-10.2C12 2.6 9.3 0 6 0z" fill="#fff"/><circle cx="6" cy="5.8" r="2.2" fill="#a7a7a7"/></svg><span>18 Palm Lane, Al Barsha<br>Dubai, UAE 00000</span></div>
    </div>
  </div>
  <div class="abs f-col" style="left:809px">
    <h5>Email subscription</h5>
    <p style="margin-top:22px;font-size:12.5px">Register your email address to get information</p>
    <div class="email-field">Email Address</div>
    <div class="subscribe">Subscribe</div>
  </div>
  <div class="abs f-rule"></div>
  <div class="abs copy">Copyright © 2018, Maren by the dunes. All Rights Reserved.</div>
  <div class="abs socials" aria-label="Social links"><span></span><span></span><span></span><span></span></div>
</footer>

</body>
</html>
```